verdant terraces simple classy business card design

my name is colin barrow and I run a gardening business aimed at high class verdant terraces. the business name is verdant terraces and our logo was designed on pixel harbour .My clientel are anything from residential homes to businesses. I take pride in my work and know that I offer a service like no other in my area.
The business card will be used to represent my business and I want it to be not only rememberable, but simplistic and modern. Eye catching too. Of course I would like it relatable to gardening and appealing to the correct clientel - those being garden enthusiasts, prestigious homes and businesses that are after top of the line gardening services like no other on the market.
I am not a typical lawn mowing business so I don't want a typical card design that represents that. The gardens I work with are generally million dollar properties with owners who are very garden proud looking for upkeep and guidance from me along with sometimes whole new garden designs. I want the business cards to show to my clients that I take pride, as they do, in their garden. And I want them to know from my card that I am a professional, qualified horticulturist offering them a top of the line service for life. I want them to refer my business on. I want them to look at my business card and see class and professionalism in a modern unique bold way.
The card should be simple with the possibility of the logo on the front being embossed/debossed and my details on the back the card should have a organic garden feel it's very important to me that it is absolutely perfect
I am also very open to ideas and suggestions so look forward to seeing the designs. the business logo has been supplied with this project and I want the card to be double sided

Contact info is
Colin Barrow - Managing Director / Horticulturist
Phone : 0481 526 704
Email: colinbarrow@verdantterraces.example.au

Target Market(s)

high class gardens residential and commercial

Industry/Entity Type

Gardener

Contact Information for Business Card

Contact info is
Phone : 0481 526 704

PLEASE MAKE CARD DOUBLE SIDED

Requirements
Must have
• organic simple classy modern feel
• must flow with the current logo that has been supplied with this project
• Double sided
• Must explain in a simple way that I deal with high end gardens and I'm a qualified horticulturist
Nice to have
• embossed debossed logo
Should not have
• shouldn't be to busy or cheap looking

```html
<!DOCTYPE html>
<html lang="en">
<head>
<meta charset="utf-8">
<title>Verdant Terraces — Business Card</title>
<link rel="stylesheet" href="https://fonts.googleapis.com/css2?family=Source+Sans+3:wght@400;600&display=swap">
<style>
  :root {
    --backdrop: #eceeec;
    --card: #ffffff;
    --leaf-green: #5e9a4f;
    --gold: #c99a2e;
    --gold-light: #e6cf93;
    --ink: #333333;
  }
  html, body {
    margin: 0;
    padding: 0;
    width: 1200px;
    height: 854px;
    overflow: hidden;
    background: var(--backdrop);
    font-family: "Source Sans 3", "Myriad Pro", sans-serif;
  }
  .card-spread {
    position: relative;
    width: 1200px;
    height: 854px;
  }
  .card {
    position: absolute;
    top: 180px;
    width: 299px;
    height: 525px;
    background: var(--card);
    box-shadow: 0 2px 6px rgba(0,0,0,0.18);
  }
  .card--details { left: 205px; }
  .card--feature { left: 606px; }
  .card svg { display: block; width: 100%; height: 100%; }
  .brand-name { fill: var(--leaf-green); font-weight: 600; }
  .holder-name { fill: var(--gold); font-size: 26px; font-weight: 400; }
  .holder-role { fill: var(--gold); font-size: 15.5px; font-weight: 400; }
  .contact-line { fill: var(--ink); font-size: 13px; font-weight: 400; }
</style>
</head>
<body>
<main class="card-spread">

  <section class="card card--details" aria-label="Card back with contact details">
    <svg viewBox="0 0 346 607" xmlns="http://www.w3.org/2000/svg">
      <defs>
        <linearGradient id="goldFrameA" x1="0" y1="0" x2="1" y2="1">
          <stop offset="0" stop-color="#c99a2e"/>
          <stop offset="0.45" stop-color="#e6cf93"/>
          <stop offset="0.75" stop-color="#d3a53b"/>
          <stop offset="1" stop-color="#e6cf93"/>
        </linearGradient>
      </defs>
      <g class="brand-lockup" text-anchor="middle">
        <text class="brand-name" x="173" y="160" font-size="36" textLength="272" lengthAdjust="spacing">VERDANT</text>
        <text class="brand-name" x="173" y="187" font-size="18" textLength="270" lengthAdjust="spacing">TERRACES</text>
      </g>
      <polygon class="hex-frame" points="173,226 328,314 328,494 173,583 18,494 18,314"
               fill="none" stroke="url(#goldFrameA)" stroke-width="4"/>
      <g text-anchor="middle">
        <text class="holder-name" x="173" y="345">Colin Barrow</text>
        <text class="holder-role" x="173" y="384">Managing Director / Horticulturist</text>
        <text class="contact-line" x="173" y="466">Phone : 0481 526 704</text>
        <text class="contact-line" x="173" y="486" textLength="290" lengthAdjust="spacingAndGlyphs">Email: colinbarrow@verdantterraces.example.au</text>
      </g>
    </svg>
  </section>

  <section class="card card--feature" aria-label="Card front with garden feature">
    <svg viewBox="0 0 346 607" xmlns="http://www.w3.org/2000/svg">
      <defs>
        <linearGradient id="goldFrameB" x1="0" y1="0" x2="1" y2="1">
          <stop offset="0" stop-color="#c99a2e"/>
          <stop offset="0.45" stop-color="#e6cf93"/>
          <stop offset="0.75" stop-color="#d3a53b"/>
          <stop offset="1" stop-color="#e6cf93"/>
        </linearGradient>
        <linearGradient id="gardenTones" x1="0" y1="0" x2="0" y2="1">
          <stop offset="0" stop-color="#3f6b36"/>
          <stop offset="0.35" stop-color="#5d7a45"/>
          <stop offset="0.55" stop-color="#8a5a44"/>
          <stop offset="0.8" stop-color="#6f9a48"/>
          <stop offset="1" stop-color="#7fae46"/>
        </linearGradient>
      </defs>
      <g class="brand-lockup" text-anchor="middle">
        <text class="brand-name" x="173" y="157" font-size="36" textLength="272" lengthAdjust="spacing">VERDANT</text>
        <text class="brand-name" x="173" y="184" font-size="18" textLength="270" lengthAdjust="spacing">TERRACES</text>
      </g>
      <polygon class="hex-frame" points="173,222 329,308 329,484 173,578 17,484 17,308"
               fill="none" stroke="url(#goldFrameB)" stroke-width="4"/>
      <polygon class="garden-feature" role="img"
               aria-label="Photograph of a formal terraced garden with stone steps, clipped hedges and a manor house"
               points="173,254 313,332 313,486 173,570 33,486 33,332"
               fill="url(#gardenTones)"/>
    </svg>
  </section>

</main>
</body>
</html>
```